Diverse, up-scale salon needs eye-catching, unique business cards.

We are looking for a unique business card design for our stylist but that can also be multi functional and used for appointment reminder and referrals. I will need a design in a format that I can modify names and titles going forward. In the past we have had a dark background with the logo on one side, and stylist and contact information on the other but we are open to all ideas. I have included our mission statement as well as branded colors below. The statement doesn't need to go on the card, it's just a reference for target market. We need space for the stylists name, title, instagram handle and then the salons phone number, website and address. I am also open to adding a spot for a qr code linked to the stylist instagram or the salon booking link.

primary brand colors:
#333333 #233415 #36502a #93874a #000000
Mission statement:
Vessolin Hair Studio, a high-end salon located in the lively Downtown Farmington, Michigan, is committed to providing exceptional services in a welcoming and relaxed environment to meet the needs of our diverse clientele.
Our salon specializes in contemporary custom haircuts, coloring, extensions, and barbering and beard grooming services. Our team of skilled stylists is passionate and inventive in their hair styling techniques. At the heart of our salon are values centered on quality, innovation, creativity, and above all, comfort. These core values are evident in every appointment across our customizable array of services.
Our goal is to establish a benchmark for exceptional hair care for every human.
Website: www.vessolinhairstudio.example
instagram: @vessolinhairstudio
address: 41782 Pelham Crest Rd, Farmington MI
phone: 248-613-4087

Industry/Entity Type

Hair Salon

Contact Information for Business Card

Stylist name, title, phone, instagram, website, address, (optional qr code)

Requirements
Should not have
• Does not need mission statement on the card.

```html
<!DOCTYPE html>
<html lang="en">
<head>
<meta charset="utf-8">
<title>Vessolin Hair Studio – Business Card</title>
<link rel="stylesheet" href="https://fonts.googleapis.com/css2?family=Lato:wght@400;700&family=Montserrat:wght@300;700&display=swap">
<style>
  :root {
    --olive: #93874a;
    --olive-dark: #7d7340;
    --paper: #ffffff;
    --ink: #333333;
    --backdrop: #2a2c2f;
  }
  * { box-sizing: border-box; margin: 0; padding: 0; }
  html, body { width: 1200px; height: 952px; overflow: hidden; }
  body {
    background: var(--backdrop);
    font-family: "Lato", sans-serif;
    position: relative;
  }
  .card {
    position: absolute;
    width: 580px;
    height: 330px;
    border-radius: 22px;
    overflow: hidden;
    box-shadow: 0 18px 40px rgba(0,0,0,.45);
  }

  /* Front: stylist details */
  .card-front { left: 560px; top: 90px; background: var(--paper); }
  .front-band {
    position: absolute; left: 0; top: 0; bottom: 0; width: 26px;
    background: var(--olive);
  }
  .name-tab {
    position: absolute; left: 0; top: 26px; width: 78px; height: 46px;
    background: var(--olive);
    border-radius: 0 23px 23px 0;
    display: flex; align-items: center; justify-content: flex-end; padding-right: 14px;
  }
  .name-tab svg { width: 22px; height: 22px; }
  .stylist {
    position: absolute; left: 96px; top: 26px;
  }
  .stylist-name {
    font-family: "Montserrat", sans-serif;
    font-size: 30px; letter-spacing: .5px; color: var(--olive);
    line-height: 1;
  }
  .stylist-name .first { font-weight: 300; }
  .stylist-name .last { font-weight: 700; }
  .stylist-title { font-size: 15px; color: var(--ink); margin-top: 6px; }

  .contacts { position: absolute; left: 52px; top: 122px; list-style: none; }
  .contacts li {
    display: flex; align-items: center; margin-bottom: 20px;
    color: var(--ink); font-size: 14px; line-height: 1.3;
  }
  .contacts .icon { width: 22px; height: 22px; flex: none; }
  .contacts .divider {
    width: 1px; height: 26px; background: var(--ink);
    transform: rotate(20deg); margin: 0 14px 0 12px; flex: none;
  }

  .brand-mark {
    position: absolute; right: 40px; bottom: 44px; width: 190px;
    display: flex; flex-direction: column; align-items: center; gap: 10px;
    text-align: center;
  }
  .brand-dot {
    width: 34px; height: 34px; border-radius: 50%;
    border: 3px solid currentColor;
  }
  .brand-name {
    font-family: "Lato", sans-serif; font-weight: 700;
    font-size: 17px; letter-spacing: 3px; text-transform: uppercase; line-height: 1.35;
  }
  .card-front .brand-mark { color: var(--olive); }

  /* Back: brand side */
  .card-back { left: 70px; top: 520px; background: var(--olive); }
  .back-tab {
    position: absolute; width: 160px; height: 34px;
    background: var(--paper); border-radius: 10px;
  }
  .back-tab.top-left { left: -10px; top: 26px; }
  .back-tab.bottom-right { right: -10px; bottom: 26px; }
  .card-back .brand-mark {
    color: var(--paper); right: auto; bottom: auto;
    left: 50%; top: 50%; transform: translate(-50%, -50%); width: 240px;
  }
  .card-back .brand-dot { width: 44px; height: 44px; }
  .card-back .brand-name { font-size: 22px; }
</style>
</head>
<body>

  <section class="card card-front" aria-label="Card front – stylist details">
    <div class="front-band"></div>
    <div class="name-tab">
      <svg viewBox="0 0 24 24" aria-hidden="true"><circle cx="12" cy="8" r="5" fill="#fff"/><path d="M3 22c0-5 4-8 9-8s9 3 9 8z" fill="#fff"/></svg>
    </div>
    <div class="stylist">
      <h1 class="stylist-name"><span class="first">MARA</span> <span class="last">KELLWOOD</span></h1>
      <p class="stylist-title">Marketing Manager</p>
    </div>

    <ul class="contacts">
      <li>
        <svg class="icon" viewBox="0 0 24 24" aria-hidden="true"><path fill="#93874a" d="M6.6 10.8a15 15 0 0 0 6.6 6.6l2.2-2.2c.3-.3.7-.4 1-.2 1.1.4 2.3.6 3.6.6.6 0 1 .4 1 1V20c0 .6-.4 1-1 1C10.6 21 3 13.4 3 4c0-.6.4-1 1-1h3.5c.6 0 1 .4 1 1 0 1.3.2 2.5.6 3.6.1.3 0 .7-.2 1z"/></svg>
        <span class="divider"></span>
        <span>248-613-4087<br>248-613-4087</span>
      </li>
      <li>
        <svg class="icon" viewBox="0 0 24 24" aria-hidden="true"><path fill="#93874a" d="M2 21 23 12 2 3v7l15 2-15 2z"/></svg>
        <span class="divider"></span>
        <span>www.vessolinhairstudio.example<br>@vessolinhairstudio</span>
      </li>
      <li>
        <svg class="icon" viewBox="0 0 24 24" aria-hidden="true"><path fill="#93874a" d="M12 3 2 12h3v8h5v-6h4v6h5v-8h3z"/></svg>
        <span class="divider"></span>
        <span>41782 Pelham Crest Rd,<br>Farmington MI</span>
      </li>
    </ul>

    <div class="brand-mark">
      <span class="brand-dot"></span>
      <span class="brand-name">Vessolin<br>Hair Studio</span>
    </div>
  </section>

  <section class="card card-back" aria-label="Card back – salon name">
    <div class="back-tab top-left"></div>
    <div class="back-tab bottom-right"></div>
    <div class="brand-mark">
      <span class="brand-dot"></span>
      <span class="brand-name">Vessolin<br>Hair Studio</span>
    </div>
  </section>

</body>
</html>
```